Web Design for company in the healthcare industry

We need a web design for a new company in the healthcare industry (telehealth) which allows patients to schedule appointments at their convenience, view and monitor their results, and consult with specialists that fit their requirements. The aim is to help patients take charge of their own health.

We already have a logo (attached) and are working with a developer who will do all the back end programming once the design is ready. Apart from the colours in the logo, we think shades of gray would work well.

Target Market(s)

I imagine the vast majority would be professionals from 30-50 years old.

Industry/Entity Type

Health And Wellness

Number of Pages Required

4 page

Requirements
Must have
• Hand-sketched graphics, particularly on landing page.
Should not have
• We don't want any photographs of people

```html
<!DOCTYPE html>
<html lang="en">
<head>
<meta charset="utf-8">
<title>Medora — Telehealth</title>
<link rel="stylesheet" href="https://fonts.googleapis.com/css2?family=Open+Sans:wght@400;600;700;800&display=swap">
<style>
:root{
  --blue:#1d5a9e;
  --blue-dark:#164a86;
  --blue-text:#2a6bb3;
  --green:#8cc63f;
  --green-dark:#6fa82a;
  --ink:#333;
  --muted:#777;
  --line:#dcdcdc;
  --footer:#2c2c2c;
  --footer-deep:#1f1f1f;
  --white:#fff;
}
*{box-sizing:border-box;margin:0;padding:0}
html,body{width:1200px;height:2192px;overflow:hidden}
body{font-family:"Open Sans",Arial,sans-serif;color:var(--ink);background:var(--white);font-size:13px}
.site-header{height:96px;display:flex;align-items:center;justify-content:space-between;padding:0 60px;border-bottom:3px solid var(--green)}
.brand{display:flex;align-items:center;gap:10px;font-size:34px;font-weight:700;color:var(--blue)}
.brand-dot{width:16px;height:16px;border-radius:50%;background:var(--green)}
.main-nav{display:flex;gap:42px;align-items:center;font-size:12px;font-weight:600;color:#666}
.main-nav a{color:inherit;text-decoration:none;padding:8px 0}
.main-nav a.active{color:var(--blue);border-bottom:2px solid var(--blue)}
.lang{border:1px solid var(--line);padding:4px 10px;font-size:11px;display:flex;gap:6px;align-items:center}
.lang span.flag{width:16px;height:10px;background:linear-gradient(#c33 0 50%,#fff 50%)}
.hero{height:504px;position:relative;background:linear-gradient(135deg,#e7edf3 0%,#b9c6d3 45%,#5d6b7a 80%,#2f3944 100%)}
.hero-arrow{position:absolute;top:232px;width:40px;height:40px;border-radius:50%;background:rgba(255,255,255,.75);display:flex;align-items:center;justify-content:center}
.hero-arrow.prev{left:20px}.hero-arrow.next{right:20px}
.welcome{height:550px;display:flex;gap:60px;padding:50px 100px 0}
.welcome-text{flex:1}
h2.section-title{font-size:26px;font-weight:600;color:var(--blue);margin-bottom:14px}
h2.section-title b{color:var(--green);font-weight:600}
.lead{color:var(--blue-text);font-size:14px;font-weight:600;line-height:1.5;margin-bottom:16px}
.body-copy{color:var(--muted);font-size:12px;line-height:1.75;margin-bottom:30px}
.btn{display:inline-block;padding:11px 26px;font-size:12px;font-weight:700;color:var(--white);text-decoration:none;letter-spacing:.5px}
.btn-blue{background:var(--blue)}
.appointment{width:320px}
.appointment h3{font-size:20px;font-weight:600;color:var(--blue);text-align:center}
.appointment p{font-size:11px;color:var(--muted);text-align:center;margin:4px 0 18px}
.field{height:38px;border:1px solid var(--line);margin-bottom:12px;padding:0 12px;display:flex;align-items:center;justify-content:space-between;font-size:11px;color:#aaa}
.field.tall{height:80px;align-items:flex-start;padding-top:10px}
.btn-green{display:block;background:var(--green);text-align:center;border-bottom:3px solid var(--green-dark)}
.services{height:450px;background:var(--blue);position:relative;color:var(--white);text-align:center;padding-top:70px}
.services .edge{position:absolute;left:0;width:1200px;height:12px}
.services .edge.top{top:0}.services .edge.bottom{bottom:0}
.services h2{font-size:28px;font-weight:600}
.services .intro{font-size:13px;line-height:1.6;margin:10px auto 34px;width:620px;color:#dce6f2}
.service-list{display:flex;justify-content:center;gap:78px}
.service{width:160px}
.service-icon{width:100px;height:100px;border-radius:50%;background:var(--green);border:4px solid #a9d96b;margin:0 auto 16px;display:flex;align-items:center;justify-content:center}
.service h4{font-size:12px;font-weight:700;margin-bottom:6px}
.service p{font-size:11px;line-height:1.5;color:#cfdcec}
.partners{height:210px;text-align:center;padding-top:36px}
.partners h2{font-size:22px;font-weight:600;color:var(--blue);margin-bottom:28px}
.partners h2 b{color:var(--green);font-weight:600}
.partner-row{display:flex;justify-content:center;gap:20px}
.partner{width:130px;height:70px;border:1px solid var(--line);display:flex;align-items:center;justify-content:center}
.partner i{display:block;width:70px;height:26px;background:#c9d2dc;border-radius:3px}
.site-footer{height:340px;background:var(--footer);color:#bbb;display:flex;gap:40px;padding:34px 60px 0}
.col{flex:1}
.col h5{color:var(--white);font-size:12px;font-weight:700;margin-bottom:16px;letter-spacing:.5px}
.socials{display:flex;gap:12px;margin-bottom:22px}
.socials i{width:14px;height:14px;background:#888;border-radius:2px}
.col p{font-size:11px;line-height:1.7;margin-bottom:14px}
.comment{border-bottom:1px solid #444;padding-bottom:12px;margin-bottom:12px;font-size:11px;line-height:1.6}
.hours{width:100%;font-size:11px;border-collapse:collapse}
.hours td{padding:3px 0}
.hours td.day{color:var(--green);font-weight:700}
.contact-line{font-size:11px;line-height:1.8}
.contact-line b{color:var(--green)}
.bottom-bar{height:42px;background:var(--footer-deep);color:#888;font-size:11px;display:flex;align-items:center;justify-content:space-between;padding:0 60px}
.bottom-bar nav{display:flex;gap:18px}
</style>
</head>
<body>
<header class="site-header">
  <div class="brand"><span>medora</span><span class="brand-dot"></span></div>
  <nav class="main-nav">
    <a class="active">HOME</a><a>ABOUT US</a><a>SERVICES</a><a>HEALTH PACKAGES</a><a>CONTACT US</a>
    <span class="lang"><span class="flag"></span>English ▾</span>
  </nav>
</header>

<section class="hero" role="img" aria-label="Stethoscope resting on a laptop keyboard">
  <span class="hero-arrow prev"><svg width="12" height="16"><path d="M9 2 3 8l6 6" stroke="#555" stroke-width="2" fill="none"/></svg></span>
  <span class="hero-arrow next"><svg width="12" height="16"><path d="M3 2l6 6-6 6" stroke="#555" stroke-width="2" fill="none"/></svg></span>
</section>

<section class="welcome">
  <div class="welcome-text">
    <h2 class="section-title">WELCOME TO <b>MEDORA</b></h2>
    <p class="lead">Book care when it suits you, follow your results online and speak with the right specialist for your needs, all from one secure place.</p>
    <p class="body-copy">Medora is a new telehealth service built for busy people who want to take charge of their own health. Choose a health package, pick a time that works for your day and meet a qualified doctor by video from home or the office. Your test results arrive in your private account, with clear notes and trends you can track over time. When you need more, we match you with a specialist who fits your situation and keeps your full history in view.<br><br>Our team checks every booking, every result and every follow-up so nothing falls through the cracks. Simple steps, clear advice and care that moves at your pace.</p>
    <a class="btn btn-blue">READ MORE</a>
  </div>
  <form class="appointment">
    <h3>REQUEST FREE APPOINTMENT</h3>
    <p>Tell us when suits you and we will call back</p>
    <div class="field">Name</div>
    <div class="field">E-mail</div>
    <div class="field">Phone</div>
    <div class="field">Type of Request <span>▾</span></div>
    <div class="field tall">Message</div>
    <a class="btn btn-green">SUBMIT FORM</a>
  </form>
</section>

<section class="services">
  <svg class="edge top" viewBox="0 0 1200 12" preserveAspectRatio="none"><path d="M0 0H1200V0 L1190 10 1180 0 1170 10 1160 0 1150 10 1140 0 1130 10 1120 0 1110 10 1100 0 1090 10 1080 0 1070 10 1060 0 1050 10 1040 0 1030 10 1020 0 1010 10 1000 0 990 10 980 0 970 10 960 0 950 10 940 0 930 10 920 0 910 10 900 0 890 10 880 0 870 10 860 0 850 10 840 0 830 10 820 0 810 10 800 0 790 10 780 0 770 10 760 0 750 10 740 0 730 10 720 0 710 10 700 0 690 10 680 0 670 10 660 0 650 10 640 0 630 10 620 0 610 10 600 0 590 10 580 0 570 10 560 0 550 10 540 0 530 10 520 0 510 10 500 0 490 10 480 0 470 10 460 0 450 10 440 0 430 10 420 0 410 10 400 0 390 10 380 0 370 10 360 0 350 10 340 0 330 10 320 0 310 10 300 0 290 10 280 0 270 10 260 0 250 10 240 0 230 10 220 0 210 10 200 0 190 10 180 0 170 10 160 0 150 10 140 0 130 10 120 0 110 10 100 0 90 10 80 0 70 10 60 0 50 10 40 0 30 10 20 0 10 10 0 0Z" fill="#fff"/></svg>
  <h2>OUR SERVICES</h2>
  <p class="intro">Four simple steps from choosing your care to feeling better, all handled online with a real team behind you.</p>
  <div class="service-list">
    <div class="service">
      <div class="service-icon"><svg width="46" height="46" viewBox="0 0 46 46"><path d="M6 14 23 6l17 8v20l-17 8-17-8z M6 14l17 8 17-8 M23 22v20" fill="none" stroke="#fff" stroke-width="3" stroke-linejoin="round"/></svg></div>
      <h4>SELECT A PACKAGE</h4><p>Browse health plans and pick the one that fits you best.</p>
    </div>
    <div class="service">
      <div class="service-icon"><svg width="46" height="46" viewBox="0 0 46 46"><rect x="6" y="9" width="34" height="31" rx="2" fill="none" stroke="#fff" stroke-width="3"/><path d="M6 17h34M14 5v8M32 5v8M13 24h5M21 24h5M29 24h5M13 31h5M21 31h5M29 31h5" stroke="#fff" stroke-width="3"/></svg></div>
      <h4>SCHEDULE APPOINTMENT</h4><p>Choose a time that works and meet your doctor online.</p>
    </div>
    <div class="service">
      <div class="service-icon"><svg width="46" height="46" viewBox="0 0 46 46"><rect x="9" y="7" width="28" height="34" rx="2" fill="none" stroke="#fff" stroke-width="3"/><path d="M17 4h12v7H17zM15 24l5 5 10-11" fill="none" stroke="#fff" stroke-width="3"/></svg></div>
      <h4>GET YOUR RESULTS</h4><p>View and track your results securely in your account.</p>
    </div>
    <div class="service">
      <div class="service-icon"><svg width="46" height="46" viewBox="0 0 46 46"><path d="M23 39 8 24a8 8 0 0 1 15-11 8 8 0 0 1 15 11z" fill="none" stroke="#fff" stroke-width="3" stroke-linejoin="round"/></svg></div>
      <h4>A HEALTHIER YOU</h4><p>Follow clear advice and take charge of your own health.</p>
    </div>
  </div>
  <svg class="edge bottom" viewBox="0 0 1200 12" preserveAspectRatio="none"><path d="M0 12H1200 L1190 2 1180 12 1170 2 1160 12 1150 2 1140 12 1130 2 1120 12 1110 2 1100 12 1090 2 1080 12 1070 2 1060 12 1050 2 1040 12 1030 2 1020 12 1010 2 1000 12 990 2 980 12 970 2 960 12 950 2 940 12 930 2 920 12 910 2 900 12 890 2 880 12 870 2 860 12 850 2 840 12 830 2 820 12 810 2 800 12 790 2 780 12 770 2 760 12 750 2 740 12 730 2 720 12 710 2 700 12 690 2 680 12 670 2 660 12 650 2 640 12 630 2 620 12 610 2 600 12 590 2 580 12 570 2 560 12 550 2 540 12 530 2 520 12 510 2 500 12 490 2 480 12 470 2 460 12 450 2 440 12 430 2 420 12 410 2 400 12 390 2 380 12 370 2 360 12 350 2 340 12 330 2 320 12 310 2 300 12 290 2 280 12 270 2 260 12 250 2 240 12 230 2 220 12 210 2 200 12 190 2 180 12 170 2 160 12 150 2 140 12 130 2 120 12 110 2 100 12 90 2 80 12 70 2 60 12 50 2 40 12 30 2 20 12 10 2 0 12Z" fill="#fff"/></svg>
</section>

<section class="partners">
  <h2>PARTNERS <b>LOGOS</b></h2>
  <div class="partner-row">
    <div class="partner"><i></i></div><div class="partner"><i></i></div><div class="partner"><i></i></div>
    <div class="partner"><i></i></div><div class="partner"><i></i></div><div class="partner"><i></i></div>
  </div>
</section>

<footer class="site-footer">
  <div class="col">
    <h5>KEEP IN TOUCH</h5>
    <div class="socials"><i></i><i></i><i></i><i></i><i></i><i></i></div>
    <p>Follow our updates for health tips, new packages and news from the Medora care team.</p>
    <p>Join our monthly letter for simple advice on staying well.</p>
  </div>
  <div class="col">
    <h5>RECENT COMMENTS</h5>
    <div class="comment">Booking took two minutes and my doctor called on time.<br>— Laura, 2 days ago</div>
    <div class="comment">Seeing my results online saved me a trip.<br>— Mark, 5 days ago</div>
  </div>
  <div class="col">
    <h5>HOURS</h5>
    <table class="hours">
      <tr><td class="day">MONDAY</td><td>8:00 AM</td><td>to</td><td>6:00 PM</td></tr>
      <tr><td class="day">TUESDAY</td><td>8:00 AM</td><td>to</td><td>6:00 PM</td></tr>
      <tr><td class="day">WEDNESDAY</td><td>8:00 AM</td><td>to</td><td>6:00 PM</td></tr>
      <tr><td class="day">THURSDAY</td><td>8:00 AM</td><td>to</td><td>6:00 PM</td></tr>
      <tr><td class="day">FRIDAY</td><td>8:00 AM</td><td>to</td><td>4:00 PM</td></tr>
    </table>
  </div>
  <div class="col">
    <h5>CONTACT US</h5>
    <p class="contact-line">120 Harbor Lane, Suite 4<br>Riverton, RV 20418</p>
    <p class="contact-line"><b>TEL:</b> +1 555 0148<br><b>FAX:</b> +1 555 0149<br><b>EMAIL:</b> care@medora-health.example</p>
  </div>
</footer>
<div class="bottom-bar">
  <span>Copyright © Medora. All Rights Reserved.</span>
  <nav><span>Home</span><span>Terms of Use &amp; Privacy Policy</span><span>Contact us</span></nav>
</div>
</body>
</html>
```